Vorabine Tessa Golim / Website

We are looking for a web design in modern baroque style for our launching on-line jewellery shop website. Through pitchhollow we have done a contest for the logo of our company, for which we have chosen the winner. See the files for the winning logo design.
Our on-line jewellery shop will sell hand made jewellery from an artist.

We will be building our site using the Ferro Wick Lane content management system.

In this contest we will need “Uncoded” files.
We expect to receive layered PSD files.
We will ask –outside this contest- a web development/designer to code it and bring it into a working web page.

The brand of our company is build around the following key words:
sophistication
smart looking
charming
nice-looking
feminine
smooth
stylish
fashionable
wearable
precious

The name of the company is Vorabine Tessa Golim, in brief VGT. We will use the website www.vorabine-example.com. The logo will bear VTG and a mask as an insigne. The style of our brand is modern baroque.

The target group of the jewellery is Young Urban Professionals, people between 25 and 40 years old.

We want a dark background and a simple stylish background, in the style of modern baroque. This does not mean that the website should be crowded by curls, but it should contain baroque elements.

The basis idea about the website design is that it works like the user is opening jewellery boxes. By each click another inside world appears which provides some nice surprises.

The home page will contain a photo of a lady showing one of the pieces of jewellery (for this photo we plan to do a photoshooting once we have the design). And it will show the names of our 10 different collections. There will be no further information. One can click on each of the collection names to go to a specific collection page.

Each collection page (see the picture for an example of a collection) will show one big picture of a main feature of the jewelery, and it will show other elements of the collection in small pictures, like the:
necklace
earrings
bracelet
ring
complete set
We can not show the other jewellery yet, but for the design of the webpages you can use any pictures of jewellery, which we will definitely will not use for the final website.

Again by clicking on each of these small pictures another page appears showing the item in a similar designed web page.

And if appropriate there should be an option to choose between different color versions of the same set, which can go in maximum three different colors.

On each of the collection page there should be a rectangular frame, which looks like a jewellery box (see the picture for the style of the box we have chosen), with a further option to go to next pages in each corner. The name of each collection should be clearly written in the page.

The keywords for the buttons will be:
Origin
Buy
Ask
Become a fan

The “Origin” page will explain the background and history of the artist and the cultural heritage is refers to. This page has also to be designed in the same style as the other pages, but will read like a story in book which can contain different chapters:
- artist interview
- design origin
- cultural heritage
- preferred usage and tips
- etc.

The “Buy” page will provide the necessary elements to order the item. For this we will use a module of FerroWickLane. The only thing needed for this page from a point of design is the background.

The “Ask” page will be on the possibility to send us an e-mail with questions. It will contain some items to be selected, but again for this page from a point of design the only thing needed for this page is the background.

The “Become a fan” page will contain the possibility to register yourself as a fan to get regular newsletters and updates by e-mail from VTG.

We like the following examples of other jewelery websites
www.plovet-example.ch
www.quibrengems-example.com

The final result we will need are layered PSD files.
Updates

We have discussed in our team the technicalities of what we actually need in this contest.

What we will need is "Uncoded" files.
Outside this contest we will ask a web developer/designer to code it and to bring it into a working web page.

We have updated our brief accordingly.

Target Market(s)

Industry/Entity Type

It Company

Requirements
Must have
• The website should be really creative and be of another nature than informative websites. It should be a pleasure and a kind of discovery to go through our website.
Nice to have
• If the web site has moving elements, than it should drag you in from one page to another, like you are opening boxes.
Should not have
• The idea is that the website is not going crazy with pop ups and moving things, but is distinguished and a pleasure to look at.

```html
<!DOCTYPE html>
<html lang="en">
<head>
<meta charset="utf-8">
<title>Vorabine Tessa Golim – Collection</title>
<link href="https://fonts.googleapis.com/css2?family=PT+Sans:wght@400;700&family=Questrial&family=Pinyon+Script&display=swap" rel="stylesheet">
<style>
  :root {
    --bg: #000000;
    --ink: #f2f2f2;
    --rule: #c8c8c8;
    --panel: #b4b4b4;
    --panel-strip: #828282;
    --panel-ink: #1c1c1c;
    --script: #7a7a7a;
    --thumb-border: #8c8c8c;
    --arrow: #a8a8a8;
  }
  html, body { margin: 0; padding: 0; background: var(--bg); overflow: hidden; }
  .page { position: relative; width: 1200px; height: 703px; background: var(--bg); overflow: hidden; font-family: "Questrial", sans-serif; }
  .rule { position: absolute; left: 62px; width: 1076px; height: 2px;
    background: linear-gradient(90deg, rgba(200,200,200,0) 0%, var(--rule) 30%, var(--rule) 70%, rgba(200,200,200,0) 100%); }
  .rule--top { top: 103px; }
  .rule--bottom { top: 570px; }
  .brand { position: absolute; left: 525px; top: 17px; width: 150px; height: 134px; background: var(--bg);
    color: var(--ink); font-family: "PT Sans", sans-serif; font-weight: 400; text-align: center; }
  .brand__mark { position: absolute; left: 0; top: 30px; width: 150px; font-size: 52px; letter-spacing: 2px; line-height: 1; }
  .brand__name { position: absolute; left: 0; top: 118px; width: 150px; font-size: 13px; line-height: 16px; }
  .nav { position: absolute; top: 134px; left: 0; font-family: "PT Sans", sans-serif; font-size: 14px; line-height: 18px; color: var(--ink); text-transform: uppercase; }
  .nav a { position: absolute; color: var(--ink); text-decoration: none; white-space: nowrap; }
  .nav a.is-active { font-weight: 700; }
  .feature { position: absolute; left: 180px; top: 180px; width: 458px; height: 345px;
    background: radial-gradient(ellipse at 30% 40%, #1d6f78 0%, #0b3238 30%, #020708 65%), #000; }
  .feature__photo { position: absolute; inset: 0;
    background: radial-gradient(ellipse at 75% 35%, rgba(40,150,160,.75) 0%, rgba(10,50,55,.5) 35%, rgba(0,0,0,0) 65%); }
  .carousel__arrow { position: absolute; top: 467px; }
  .thumb { position: absolute; top: 451px; width: 52px; height: 52px; border: 1px solid var(--thumb-border); }
  .thumb--1 { left: 272px; background: radial-gradient(circle, #2a8a92 0%, #0a2a2e 70%); }
  .thumb--2 { left: 345px; background: radial-gradient(circle, #6e7e8c 0%, #15181c 70%); }
  .thumb--3 { left: 417px; background: radial-gradient(circle, #7a5a78 0%, #161016 70%); }
  .thumb--4 { left: 490px; background: radial-gradient(circle, #8c6a86 0%, #181218 70%); }
  .box { position: absolute; left: 638px; top: 180px; width: 385px; height: 345px; background: var(--panel); }
  .box__strip { position: absolute; left: 0; top: 0; width: 91px; height: 345px;
    background: radial-gradient(ellipse at 70% 40%, #4a9aa2 0%, #5e7e82 30%, var(--panel-strip) 60%); }
  .box__kicker { position: absolute; right: 22px; top: 8px; font-family: "Pinyon Script", cursive; font-size: 42px; line-height: 48px; color: var(--script); margin: 0; font-weight: 400; }
  .box__title { position: absolute; left: 114px; top: 70px; margin: 0; font-size: 18px; line-height: 24px; font-weight: 400; color: var(--panel-ink); }
  .box__text { position: absolute; left: 114px; top: 118px; width: 250px; margin: 0; font-size: 14px; line-height: 22.5px; color: var(--panel-ink); }
  .ornament { position: absolute; left: 564px; top: 555px; width: 64px; height: 33px; background: radial-gradient(ellipse, #8a8a8a 0%, #000 70%); }
  .footer { position: absolute; left: 0; top: 605px; width: 1200px; text-align: center; color: var(--ink); font-size: 14px; line-height: 22.5px; }
  .footer p { margin: 0; }
</style>
</head>
<body>
<div class="page">
  <div class="rule rule--top"></div>
  <div class="brand">
    <span class="brand__mark">VTG</span>
    <span class="brand__name">Vorabine</span>
  </div>

  <nav class="nav">
    <a class="is-active" href="#" style="left:207px">Collection</a>
    <a href="#" style="left:316px">Origin</a>
    <a href="#" style="left:388px">Buy</a>
    <a href="#" style="left:857px">Ask</a>
    <a href="#" style="left:909px">Become a fan</a>
  </nav>

  <div class="feature" role="img" aria-label="Close-up photo of turquoise crystal beaded jewellery on a dark reflective surface">
    <div class="feature__photo"></div>
  </div>

  <svg class="carousel__arrow" style="left:225px" width="20" height="24" viewBox="0 0 20 24" aria-label="Previous">
    <polyline points="16,2 5,12 16,22" fill="none" stroke="var(--arrow)" stroke-width="5"/>
  </svg>
  <div class="thumb thumb--1" role="img" aria-label="Thumbnail of turquoise beaded set"></div>
  <div class="thumb thumb--2" role="img" aria-label="Thumbnail of crystal bow pendant"></div>
  <div class="thumb thumb--3" role="img" aria-label="Thumbnail of pink bow necklace"></div>
  <div class="thumb thumb--4" role="img" aria-label="Thumbnail of pink butterfly pendant"></div>
  <svg class="carousel__arrow" style="left:574px" width="20" height="24" viewBox="0 0 20 24" aria-label="Next">
    <polyline points="4,2 15,12 4,22" fill="none" stroke="var(--arrow)" stroke-width="5"/>
  </svg>

  <section class="box">
    <div class="box__strip" role="img" aria-label="Faded edge of the turquoise jewellery photo"></div>
    <h2 class="box__kicker">Complete Set</h2>
    <h1 class="box__title">Teal Verano</h1>
    <p class="box__text">Silver wire has been formed into elongated hoops and asymmetrically embellished with displays of different materials and beautiful shades of turquoise. Total length is 75mm.</p>
  </section>

  <div class="rule rule--bottom"></div>
  <div class="ornament" role="img" aria-label="Baroque scroll ornament"></div>

  <footer class="footer">
    <p>Copyright (c) www.vorabine-example.com 2011</p>
    <p>Allright reserved</p>
  </footer>
</div>
</body>
</html>
```